Mastering Modern Vineyard Management

size of the ad - 8”x 10.75" plus 0.25" bleed
I would like an ad for a magazine that will stand out and make people want to read the ad.
The ad should not be crowded and people reading the ad will be able to read the text.
I would like it to be a creative and modern-day design.
the list of topics should not be the focus of the ad.
the text is attached.
If you decide to use people in the ad then please no ladies.
please note that leave over 1 inch for the bottom of the footer

```html
<!DOCTYPE html>
<html lang="en">
<head>
<meta charset="utf-8">
<title>Vineyard Management Course – Magazine Ad</title>
<link rel="stylesheet" href="https://fonts.googleapis.com/css2?family=Poppins:wght@400;500;600;700;800;900&display=swap">
<style>
  :root {
    --page-bg: #e9edf2;
    --navy-deep: #07122b;
    --navy: #0d1f45;
    --navy-mid: #183466;
    --blue-bright: #2b8be8;
    --blue: #1f78d6;
    --blue-text: #2f8cf0;
    --white: #ffffff;
    --muted: #d6e0ee;
    --rule: rgba(255,255,255,0.7);
  }
  * { margin: 0; padding: 0; box-sizing: border-box; }
  html, body {
    width: 1200px; height: 2400px; overflow: hidden;
    background: var(--page-bg);
    font-family: "Poppins", sans-serif;
  }
  .ad {
    position: absolute; left: 50px; top: 466px;
    width: 1100px; height: 1467px; overflow: hidden;
    background: var(--navy-deep);
    box-shadow: 0 10px 40px rgba(0,0,0,0.25);
    color: var(--white);
  }
  .backdrop-vineyard {
    position: absolute; inset: 0;
    background:
      radial-gradient(ellipse at 70% 75%, rgba(40,70,120,0.45), transparent 60%),
      linear-gradient(180deg, var(--navy) 0%, var(--navy-deep) 45%, #0a1833 100%);
  }
  .hero-photo {
    position: absolute; right: 0; top: 0; width: 620px; height: 611px;
    background:
      radial-gradient(ellipse at 62% 60%, rgba(150,165,190,0.55), transparent 35%),
      radial-gradient(ellipse at 70% 15%, rgba(120,140,175,0.5), transparent 45%),
      linear-gradient(90deg, rgba(13,31,69,0) 0%, var(--navy-mid) 45%, #2a3f66 100%);
  }
  .title { position: absolute; left: 52px; top: 100px; line-height: 0.86; font-weight: 800; }
  .title-lead { display: block; font-size: 212px; color: var(--blue-bright); letter-spacing: -6px; font-weight: 900; }
  .title-rest { display: block; font-size: 140px; letter-spacing: -4px; color: var(--white); }

  .band { position: absolute; left: 0; top: 611px; width: 1100px; height: 246px; display: flex; }
  .band-course { width: 529px; background: var(--blue-bright); padding: 46px 0 0 65px;
    font-size: 42px; font-weight: 800; line-height: 1.1; }
  .band-quote { flex: 1; background: var(--blue); padding: 34px 0 0 46px;
    font-size: 43px; font-weight: 800; line-height: 1.02; }

  .details { position: absolute; left: 67px; top: 892px; width: 953px; height: 65px;
    border: 2px dashed var(--rule); border-radius: 4px; display: flex; align-items: center; }
  .details-place { width: 300px; height: 100%; text-align: center; line-height: 61px;
    font-size: 44px; font-weight: 700; border-right: 2px dashed var(--rule); }
  .details-date { flex: 1; text-align: center; font-size: 46px; font-weight: 700; letter-spacing: -0.5px; }

  .perk { position: absolute; top: 975px; display: flex; align-items: center; gap: 8px;
    font-size: 27px; font-weight: 600; }
  .perk svg { width: 26px; height: 26px; }
  .perk-sessions { left: 65px; }
  .perk-scholarship { left: 593px; }

  .offer-label { position: absolute; left: 50px; top: 1034px; font-weight: 800; line-height: 0.95; }
  .offer-label-early { display: block; font-size: 36px; color: var(--blue-text); }
  .offer-label-special { display: block; font-size: 45px; }
  .offer-bar { position: absolute; left: 266px; top: 1045px; width: 754px; height: 78px;
    background: var(--blue); border-radius: 8px; padding: 10px 0 0 28px;
    font-size: 29px; font-weight: 700; line-height: 1.1; }

  .topics-heading { position: absolute; left: 51px; top: 1144px; font-size: 32px; font-weight: 700; }
  .topics-heading span { color: var(--blue-text); }
  .topic-list { position: absolute; top: 1200px; list-style: none; font-size: 18.5px; line-height: 24px; color: var(--muted); }
  .topic-list li { display: flex; align-items: center; gap: 7px; }
  .topic-list svg { width: 14px; height: 14px; flex: none; }
  .topic-list-a { left: 51px; }
  .topic-list-b { left: 432px; }
  .topic-list-c { left: 756px; top: 1206px; }
</style>
</head>
<body>
<svg width="0" height="0" style="position:absolute">
  <defs>
    <symbol id="tick-solid" viewBox="0 0 24 24"><circle cx="12" cy="12" r="12" fill="#2f8cf0"/><path d="M6.5 12.5l3.6 3.5 7.4-7.6" fill="none" stroke="#fff" stroke-width="2.6" stroke-linecap="round" stroke-linejoin="round"/></symbol>
    <symbol id="tick-line" viewBox="0 0 24 24"><circle cx="12" cy="12" r="10" fill="none" stroke="#2f8cf0" stroke-width="2"/><path d="M7.5 12.5l3 3 6-6.5" fill="none" stroke="#2f8cf0" stroke-width="2.2" stroke-linecap="round" stroke-linejoin="round"/></symbol>
  </defs>
</svg>

<main class="ad">
  <div class="backdrop-vineyard" role="img" aria-label="Dark blue aerial dusk view of vineyard rows"></div>
  <div class="hero-photo" role="img" aria-label="Man in a suit holding a miniature vineyard between his hands"></div>

  <h1 class="title">
    <span class="title-lead">VINE</span>
    <span class="title-rest">YARD</span>
    <span class="title-rest">COURSE</span>
  </h1>

  <section class="band">
    <div class="band-course">MASTERING<br>MODERN VINEYARD<br>MANAGEMENT</div>
    <div class="band-quote">INVESTING IN<br>KNOWLEDGE IS<br>INVESTING<br>INOPPORTUNITIES.</div>
  </section>

  <div class="details">
    <div class="details-place">BROOKVALE</div>
    <div class="details-date">STARTING FEBRUARY 28TH</div>
  </div>

  <div class="perk perk-sessions"><svg><use href="#tick-solid"/></svg>10 -Tuesday evenings sessions</div>
  <div class="perk perk-scholarship"><svg><use href="#tick-solid"/></svg>Limited Partial Scholarships</div>

  <div class="offer-label">
    <span class="offer-label-early">EARLY BIRD</span>
    <span class="offer-label-special">SPECIAL</span>
  </div>
  <div class="offer-bar">FOR THOSE THAT STARTED OR WOULD LIKE TO<br>GO INTO WINE GROWING</div>

  <h2 class="topics-heading"><span>TOPICS:</span> PARTIAL LISTING</h2>
  <ul class="topic-list topic-list-a">
    <li><svg><use href="#tick-line"/></svg>Vine planting and trellis plans</li>
    <li><svg><use href="#tick-line"/></svg>Soil testing</li>
    <li><svg><use href="#tick-line"/></svg>Irrigation</li>
    <li><svg><use href="#tick-line"/></svg>Pruning</li>
  </ul>
  <ul class="topic-list topic-list-b">
    <li><svg><use href="#tick-line"/></svg>Canopy management</li>
    <li><svg><use href="#tick-line"/></svg>Pest and disease basics</li>
    <li><svg><use href="#tick-line"/></svg>Harvest timing</li>
  </ul>
  <ul class="topic-list topic-list-c">
    <li><svg><use href="#tick-line"/></svg>Grape varieties</li>
    <li><svg><use href="#tick-line"/></svg>Working with wineries</li>
    <li><svg><use href="#tick-line"/></svg>Crop budgeting</li>
  </ul>
</main>
</body>
</html>
```